Zeltrova - Clever Automation

We are a software house for Audio Visual Systems integration/automation and home automation. we develop innovative software to automate a variety of devices mainly related to audio visuals and we design touch panel user interfaces to control these systems.

We would like to see designs that stick to our colours and theme, which you can find on our webpage www.zeltrova.com.au

The final design should communicate touch panels, innovation, software and automation.

Industry/Entity Type

Software

Requirements
Must have
• The business card must show the following information:
Name example : Derek Thalwin
Qualification example: B Eng ICT(CompSys) Dip EngPrac
Title example : Control Systems Programmer
Mobile Phone, Company phone, Email address ,Company website

```html
<!DOCTYPE html>
<html lang="en">
<head>
<meta charset="utf-8">
<title>Zeltrova – Business Card</title>
<link rel="stylesheet" href="https://fonts.googleapis.com/css2?family=Questrial&family=Montserrat:wght@600;700&display=swap">
<style>
  :root {
    --backdrop: #d9d9d9;
    --brand-green: #1f9a5c;
    --brand-green-dark: #157a46;
    --brand-blue: #2f86c8;
    --card-white: #ffffff;
    --ink: #333333;
    --ink-soft: #555555;
  }
  * { box-sizing: border-box; margin: 0; padding: 0; }
  html, body { width: 1200px; height: 871px; overflow: hidden; }
  body {
    background: var(--backdrop);
    font-family: "Questrial", sans-serif;
    position: relative;
  }
  .card {
    position: absolute;
    width: 560px;
    height: 320px;
    overflow: hidden;
    box-shadow: 0 8px 22px rgba(0,0,0,0.18);
  }
  .card-front {
    left: 60px; top: 90px;
    background: linear-gradient(135deg, var(--brand-green) 0%, var(--brand-green-dark) 100%);
    display: flex; align-items: center; justify-content: center;
  }
  .brand { display: flex; align-items: center; gap: 14px; }
  .brand-mark { width: 46px; height: 46px; border-radius: 6px; }
  .brand-text { display: flex; flex-direction: column; align-items: flex-end; }
  .brand-name { font-size: 48px; line-height: 1; letter-spacing: 0.5px; }
  .brand-tagline { font-size: 10px; margin-top: 3px; }

  .card-front .brand-mark { background: var(--card-white); }
  .card-front .brand-name,
  .card-front .brand-tagline { color: var(--card-white); }

  .card-back {
    left: 580px; top: 460px;
    background: var(--card-white);
  }
  .card-back .brand {
    position: absolute; left: 34px; top: 112px; gap: 10px;
  }
  .card-back .brand-mark { width: 38px; height: 38px; background: var(--brand-blue); }
  .card-back .brand-name { font-size: 36px; color: var(--brand-green); }
  .card-back .brand-tagline { font-size: 8px; color: var(--ink-soft); }

  .contact-block { position: absolute; left: 290px; top: 92px; }
  .person-name {
    font-family: "Montserrat", sans-serif; font-weight: 700;
    font-size: 17px; letter-spacing: 1.5px; color: var(--ink);
  }
  .person-qual { font-family: "Questrial", sans-serif; font-weight: 400; font-size: 11px; letter-spacing: 0.5px; }
  .person-title {
    font-family: "Montserrat", sans-serif; font-weight: 600;
    font-size: 12px; letter-spacing: 1.4px; color: var(--brand-green);
    margin-top: 2px;
  }
  .contact-list { list-style: none; margin-top: 14px; }
  .contact-list li {
    display: flex; align-items: center; gap: 10px;
    font-size: 12.5px; color: var(--ink); margin-bottom: 7px;
  }
  .contact-icon { width: 11px; height: 11px; fill: var(--brand-green); flex: none; }
  .website { font-size: 13px; color: var(--brand-green); margin-top: 4px; }
  .website span { color: var(--brand-blue); }
  .card-band { position: absolute; left: 0; bottom: 0; width: 560px; height: 34px; }
</style>
</head>
<body>
  <section class="card card-front" aria-label="Card front">
    <div class="brand">
      <div class="brand-mark"></div>
      <div class="brand-text">
        <span class="brand-name">zeltrova</span>
        <span class="brand-tagline">Clever Automation</span>
      </div>
    </div>
  </section>

  <section class="card card-back" aria-label="Card back">
    <div class="brand">
      <div class="brand-mark"></div>
      <div class="brand-text">
        <span class="brand-name">zeltrova</span>
        <span class="brand-tagline">Clever Automation</span>
      </div>
    </div>

    <div class="contact-block">
      <p class="person-name">Derek Thalwin, <span class="person-qual">B Eng ICT</span></p>
      <p class="person-title">Control Systems Programmer</p>
      <ul class="contact-list">
        <li>
          <svg class="contact-icon" viewBox="0 0 12 12"><path d="M1 4c0-2 2-3 5-3s5 1 5 3l-2 1-1-2H4L3 5zM2 6h8l1 5H1z"/></svg>
          1.877.555.0148
        </li>
        <li>
          <svg class="contact-icon" viewBox="0 0 12 12"><rect x="3" y="0.5" width="6" height="11" rx="1.2"/><rect x="4" y="2" width="4" height="6" fill="#fff"/></svg>
          604.555.0172
        </li>
        <li>
          <svg class="contact-icon" viewBox="0 0 12 12"><rect x="0.5" y="2" width="11" height="8" rx="1"/><path d="M1 3l5 4 5-4" stroke="#fff" stroke-width="1.2" fill="none"/></svg>
          dt@brightnesthome.ca
        </li>
      </ul>
      <p class="website">www.<span>zeltrova</span>.ca</p>
    </div>

    <svg class="card-band" viewBox="0 0 560 34" preserveAspectRatio="none">
      <rect x="0" y="18" width="290" height="16" fill="var(--brand-green)"/>
      <path d="M270 34 C270 18 282 8 305 8 H560 V34 Z" fill="var(--brand-blue)"/>
      <path d="M262 34 C262 16 276 4 305 4 H560 V8 H305 C282 8 270 18 270 34 Z" fill="var(--card-white)"/>
    </svg>
  </section>
</body>
</html>
```